Brisbane IT support business needs our first website

Hi All,

We are after a new website design for our IT solutions and support business.The business name is Harbourline Computing Services Group, or HCSG for short. We provide a range of solutions and services within the IT space.

I would like to utilize the two colours in our business logo I have uploaded.

I understand this is initially for the design only aspect of the site, but I would like to engage the winner to finish coding the website and finalize after also.

Target Market(s)

Other businesses owners and home users.

Industry/Entity Type

Business

Requirements
Must have
• Nice clean and functional design utilizing our business colours from the logo.

```html
<!DOCTYPE html>
<html lang="en">
<head>
<meta charset="utf-8">
<title>HCSG – Harbourline Computing Services Group</title>
<link href="https://fonts.googleapis.com/css2?family=Oxygen:wght@400;700&family=Ubuntu:ital,wght@0,500;1,500&display=swap" rel="stylesheet">
<style>
:root{
  --navy:#0d4a6b;
  --orange:#e8791e;
  --text:#3a3a3a;
  --muted:#777;
  --rule:#dcdcdc;
  --panel:#ececec;
  --footer:#333333;
  --footer-base:#444444;
}
*{box-sizing:border-box;margin:0;padding:0}
html,body{width:830px;height:1200px;overflow:hidden}
body{position:relative;background:#fff;font-family:"Oxygen",sans-serif;color:var(--text)}
.abs{position:absolute}
.top-rule{left:0;top:0;width:830px;height:3px;background:var(--navy)}

/* header */
.brand{left:95px;top:30px;width:200px;font-family:"Oxygen",sans-serif;font-weight:700;font-size:17px;line-height:22px;color:var(--navy)}
.callout{right:95px;top:16px;font-size:15px;color:#444}
.social{right:95px;top:50px;display:flex;gap:7px}
.social span{width:27px;height:27px;border-radius:50%;background:#e6e6e6;box-shadow:0 2px 3px rgba(0,0,0,.25)}
.social span.on{background:var(--orange)}

.nav{left:95px;top:97px;width:640px;display:flex;justify-content:space-between;font-size:9.5px;text-transform:uppercase;color:#333}
.nav li{list-style:none;position:relative}
.nav li.sep{color:#999;font-size:7px;padding-top:2px}
.nav li.active{color:var(--orange)}
.nav li.active::after{content:"";position:absolute;left:-3px;right:-3px;top:19px;height:3px;background:var(--orange)}

/* hero */
.hero{left:0;top:121px;width:830px;height:327px;background:linear-gradient(90deg,#b7c3cc 0%,#dfe4e8 45%,#f1ece6 70%,#e6e9ec 100%)}
.hero-title{left:96px;top:200px;font-size:19.5px;font-weight:700;color:var(--navy);line-height:1.3}
.dots{left:96px;top:381px;display:flex;gap:7px}
.dots span{width:11px;height:11px;border-radius:50%;border:1px solid #fff}
.dots span.on{background:var(--orange);border-color:#f4b27a}

.band{left:0;top:446px;width:830px;height:4px;background:var(--navy)}
.service{top:420px;width:110px;text-align:center;font-size:10px;color:#333}
.service .disc{width:52px;height:52px;margin:0 auto 10px;border-radius:50%;background:var(--navy);border:3px solid #fff;box-shadow:0 2px 4px rgba(0,0,0,.35);display:flex;align-items:center;justify-content:center}
.service.active .disc{background:var(--orange);width:58px;height:58px;margin-top:-3px;margin-bottom:7px}

/* section heading */
.heading{font-family:"Ubuntu",sans-serif;font-style:italic;font-weight:500;font-size:17px;color:#333;border-bottom:1px solid var(--rule);padding-bottom:4px}
.heading .deco{position:absolute;right:0;top:8px;width:22px;height:12px}

.about{left:96px;top:526px;width:410px}
.about p{font-size:9.6px;line-height:17.6px;margin-top:12px}
.about p+p{margin-top:17px}
.more{left:441px;top:702px;font-size:10px;color:var(--orange)}

.team{left:531px;top:515px;width:204px;height:204px;border-radius:50%;border:4px solid var(--orange);overflow:hidden;box-shadow:0 8px 10px -6px rgba(0,0,0,.35)}
.team .photo{position:absolute;inset:0;background:linear-gradient(180deg,#f2f2f2 0%,#c9d4de 55%,#8aa0b3 100%)}
.team .label{position:absolute;left:0;right:0;bottom:0;height:62px;background:var(--orange);color:#fff;text-align:center;font-size:21px;padding-top:8px}

/* lower panels */
.col-head{top:747px;width:306px}
.panel{top:782px;width:306px;height:222px;background:var(--panel);border:1px solid #d6d6d6;box-shadow:0 4px 6px rgba(0,0,0,.15);border-radius:2px}
.quote{position:absolute;left:10px;width:286px;height:104px}
.quote .avatar{position:absolute;left:10px;top:0;width:62px;height:62px;border-radius:50%;background:linear-gradient(180deg,#d9d9d9,#8f8f8f);border:3px solid #fff;box-shadow:0 1px 3px rgba(0,0,0,.3)}
.quote .who{position:absolute;left:0;top:66px;width:84px;text-align:center;font-size:11.5px;color:#333}
.quote .who small{display:block;font-size:9px;color:var(--muted);margin-top:3px}
.quote .body{position:absolute;left:98px;top:8px;width:190px;font-size:9px;line-height:12.6px;border-left:1px solid #d0d0d0;padding-left:16px}
.quote .body p+p{margin-top:5px}
.qmark{position:absolute;font-size:24px;color:#999;font-family:Georgia,serif;line-height:1}
.news{position:absolute;left:20px;width:270px;height:60px}
.news .date{position:absolute;left:48px;top:0;font-size:9.5px;font-weight:700;color:var(--orange)}
.news .text{position:absolute;left:48px;top:16px;font-size:9px;line-height:13px;width:220px}
.news.split{border-bottom:1px solid #d8d8d8}
.pager{top:1010px;display:flex;gap:6px}
.pager span{width:14px;height:14px;border-radius:50%;border:1px solid #555;font-size:11px;line-height:11px;text-align:center;color:#555}

.skyline{left:0;top:1020px;width:830px;height:25px;background:linear-gradient(180deg,#fff,#e9e9e9)}

/* footer */
.footer{left:0;top:1045px;width:830px;height:118px;background:var(--footer);color:#eee}
.footer h4{position:absolute;top:12px;font-size:13px;font-weight:400}
.links{position:absolute;top:36px;font-size:9px;line-height:18px;list-style:none}
.links li::before{content:"›";margin-right:8px}
.divider{position:absolute;top:40px;width:1px;height:56px;background:#4a4a4a}
.signup{position:absolute;left:345px;top:38px;width:130px;font-size:9px;line-height:11px}
.signup .field{margin-top:5px;width:113px;height:16px;background:#fff;border-radius:2px;color:#999;font-size:7.5px;padding:3px 5px}
.signup .btn{margin-top:9px;width:53px;height:17px;background:var(--orange);color:#fff;font-size:9px;font-weight:700;text-align:center;line-height:17px;border-radius:2px}
.map{position:absolute;left:537px;top:40px;width:80px;height:62px;background:linear-gradient(135deg,#dfe3d8,#c8d0c2)}
.contact{position:absolute;left:630px;top:40px;font-size:8.5px;line-height:11px}
.contact .row{display:flex;gap:8px;margin-bottom:5px}
.contact svg{flex:none;margin-top:1px}
.base{left:0;top:1163px;width:830px;height:37px;background:var(--footer-base);color:#ddd;font-size:8.5px;text-align:center;line-height:13px;padding-top:6px}
</style>
</head>
<body>
<div class="abs top-rule"></div>

<header>
  <div class="abs brand">Harbourline Computing<br>Services Group</div>
  <div class="abs callout">CALL US FREE: (123) 456 7890</div>
  <div class="abs social" aria-label="Social links"><span class="on"></span><span></span><span></span><span></span></div>
  <ul class="abs nav">
    <li class="active">Home</li><li class="sep">▼</li>
    <li>About Us</li><li class="sep">▼</li>
    <li>Services</li><li class="sep">▼</li>
    <li>Technology</li><li class="sep">▼</li>
    <li>Solutions</li><li class="sep">▼</li>
    <li>Support</li><li class="sep">▼</li>
    <li>Contact Us</li>
  </ul>
</header>

<section>
  <div class="abs hero" role="img" aria-label="Smiling businesswoman in a bright office with colleagues blurred behind"></div>
  <h1 class="abs hero-title">We provide a range of Solutions and<br>Services within the IT Space</h1>
  <div class="abs dots"><span class="on"></span><span></span><span></span><span></span></div>
  <div class="abs band"></div>

  <div class="abs service" style="left:100px"><div class="disc">
    <svg width="26" height="26" viewBox="0 0 26 26" fill="none" stroke="#fff" stroke-width="2.2"><path d="M5 15v-3a8 8 0 0 1 16 0v3"/><rect x="3" y="13" width="4" height="7" rx="1" fill="#fff"/><rect x="19" y="13" width="4" height="7" rx="1" fill="#fff"/><path d="M21 20q0 3-6 3"/></svg>
  </div>IT Support</div>
  <div class="abs service" style="left:229px"><div class="disc">
    <svg width="24" height="24" viewBox="0 0 24 24" fill="#fff"><path d="M4 8h5a3 3 0 1 1 6 0h5v5a3 3 0 1 0 0 6v3H4z"/></svg>
  </div>IT Solutions</div>
  <div class="abs service active" style="left:356px"><div class="disc">
    <svg width="34" height="26" viewBox="0 0 34 26" fill="#fff"><path d="M9 22a7 7 0 0 1 0-14 9 9 0 0 1 17 2 6 6 0 0 1-1 12z"/><path d="M17 9l-5 5h3v6h4v-6h3z" fill="var(--orange)"/></svg>
  </div>Harbourline Cloud</div>
  <div class="abs service" style="left:487px"><div class="disc">
    <svg width="24" height="22" viewBox="0 0 24 22" fill="none" stroke="#fff" stroke-width="2"><rect x="2" y="2" width="20" height="18"/><path d="M5 15l5-5 4 3 6-7"/></svg>
  </div>Business Solutions</div>
  <div class="abs service" style="left:608px"><div class="disc">
    <svg width="28" height="28" viewBox="0 0 28 28" fill="none" stroke="#fff" stroke-width="2.5" stroke-dasharray="3 2"><circle cx="11" cy="11" r="6"/><circle cx="20" cy="20" r="4"/></svg>
  </div>Managed Services</div>
</section>

<section class="abs about">
  <h2 class="heading" style="position:relative">ABOUT US
    <svg class="deco" viewBox="0 0 22 12" fill="var(--navy)"><rect x="0" y="8" width="3" height="3"/><rect x="5" y="8" width="3" height="3"/><rect x="10" y="8" width="3" height="3"/><rect x="14" y="4" width="3" height="3"/><rect x="19" y="0" width="3" height="3"/></svg>
  </h2>
  <p>Lorem ipsum dolor sit amet, consectetuer adipiscing elit, sed diam nonummy nibh euismod tincidunt ut laoreet dolore magna aliquam erat volutpat. Ut wisi enim ad minim venia m, quis nostrud exerci tation ullamcorper suscipit lobortis nisl ut aliquip ex ea comsed diam nonummy nibh euism od tincidunt ut laoreet dolore magna aliquam erat volutpat.</p>
  <p>Lorem ipsum dolor sit amet, consectetuer adipiscing elit, sed diam nonummy nibh euismod tincidunt ut laoreet dolore magna aliquam erat volutpat. Ut wisi enim ad minim venia m, quis nostrud....</p>
</section>
<a class="abs more">READ MORE...</a>

<div class="abs team">
  <div class="photo" role="img" aria-label="Group photo of the company team in office attire"></div>
  <div class="label">OUR TEAM</div>
</div>

<section>
  <h2 class="abs heading col-head" style="left:95px">TESTIMONIALS
    <svg class="deco" viewBox="0 0 22 12" fill="var(--navy)"><rect x="0" y="8" width="3" height="3"/><rect x="5" y="8" width="3" height="3"/><rect x="10" y="8" width="3" height="3"/><rect x="14" y="4" width="3" height="3"/><rect x="19" y="0" width="3" height="3"/></svg>
  </h2>
  <div class="abs panel" style="left:95px">
    <div class="quote" style="top:12px">
      <div class="avatar" role="img" aria-label="Portrait of client" style="left:11px"></div>
      <div class="who">Daniel Reeve<small>Businessman</small></div>
      <span class="qmark" style="left:107px;top:2px">“</span>
      <div class="body"><p>Lorem ipsum dolor sit amet, consectetuer adipiscing elit, sed diam nonummy nibh euismod tincidunt</p><p>ut laoreet dolore magnarpl aliquam erat volutpat. Ut wisi enim adm minim.</p></div>
      <span class="qmark" style="left:272px;top:78px">”</span>
    </div>
    <div style="position:absolute;left:100px;top:110px;width:180px;height:1px;background:#d8d8d8"></div>
    <div class="quote" style="top:120px">
      <div class="avatar" role="img" aria-label="Portrait of client" style="left:11px"></div>
      <div class="who">Daniel Reeve<small>Businessman</small></div>
      <span class="qmark" style="left:107px;top:2px">“</span>
      <div class="body"><p>Lorem ipsum dolor sit amet, consectetuer adipiscing elit, sed diam nonummy nibh euismod tincidunt</p><p>ut laoreet dolore magnarpl aliquam erat volutpat. Ut wisi enim adm minim.</p></div>
      <span class="qmark" style="left:272px;top:78px">”</span>
    </div>
  </div>
  <div class="abs pager" style="left:223px"><span>‹</span><span>›</span></div>

  <h2 class="abs heading col-head" style="left:429px">LATEST NEWS
    <svg class="deco" viewBox="0 0 22 12" fill="var(--navy)"><rect x="0" y="8" width="3" height="3"/><rect x="5" y="8" width="3" height="3"/><rect x="10" y="8" width="3" height="3"/><rect x="14" y="4" width="3" height="3"/><rect x="19" y="0" width="3" height="3"/></svg>
  </h2>
  <div class="abs panel" style="left:429px">
    <div class="news split" style="top:16px">
      <svg class="abs" style="left:4px;top:0" width="28" height="30" viewBox="0 0 28 30" fill="none" stroke="#666" stroke-width="2"><rect x="1" y="4" width="26" height="25" rx="2"/><path d="M1 11h26M8 1v6M20 1v6"/><path d="M6 16h3M12 16h3M18 16h3M6 22h3M12 22h3M18 22h3" stroke-width="3"/></svg>
      <div class="date">31-OCT-2014</div>
      <div class="text">Lorem ipsum dolor sit amet, consectetuer adipiscil ng elit, sed diam nonummy nibh...</div>
    </div>
    <div class="news split" style="top:90px">
      <svg class="abs" style="left:4px;top:0" width="28" height="30" viewBox="0 0 28 30" fill="none" stroke="#666" stroke-width="2"><rect x="1" y="4" width="26" height="25" rx="2"/><path d="M1 11h26M8 1v6M20 1v6"/><path d="M6 16h3M12 16h3M18 16h3M6 22h3M12 22h3M18 22h3" stroke-width="3"/></svg>
      <div class="date">30-OCT-2014</div>
      <div class="text">Lorem ipsum dolor sit amet, consectetuer adipiscil ng elit, sed diam nonummy nibh...</div>
    </div>
    <div class="news" style="top:164px">
      <svg class="abs" style="left:4px;top:0" width="28" height="30" viewBox="0 0 28 30" fill="none" stroke="#666" stroke-width="2"><rect x="1" y="4" width="26" height="25" rx="2"/><path d="M1 11h26M8 1v6M20 1v6"/><path d="M6 16h3M12 16h3M18 16h3M6 22h3M12 22h3M18 22h3" stroke-width="3"/></svg>
      <div class="date">29-OCT-2014</div>
      <div class="text">Lorem ipsum dolor sit amet, consectetuer adipiscil ng elit, sed diam nonummy nibh...</div>
    </div>
  </div>
  <div class="abs pager" style="left:565px"><span>‹</span><span>›</span></div>
</section>

<div class="abs skyline" role="img" aria-label="Faint city skyline strip"></div>

<footer class="abs footer">
  <h4 style="left:95px">Quick Links</h4>
  <ul class="links" style="left:95px"><li>HOME</li><li>ABOUT US</li><li>SERVICES</li><li>TECHNOLOGY</li></ul>
  <ul class="links" style="left:210px"><li>SOLUTIONS</li><li>SUPPORT</li><li>CONTACT US</li></ul>
  <div class="divider" style="left:311px"></div>
  <h4 style="left:345px">Newsletter Signup</h4>
  <div class="signup">Lorem ipsum dolor sit amet, consectetuer adipiscing elit.
    <div class="field">Enter your email address</div>
    <div class="btn">SUBMIT</div>
  </div>
  <div class="divider" style="left:504px"></div>
  <h4 style="left:537px">Contact Info</h4>
  <div class="map" role="img" aria-label="Small street map showing the office location"></div>
  <div class="contact">
    <div class="row"><svg width="9" height="12" viewBox="0 0 9 12" fill="var(--orange)"><path d="M4.5 0a4.5 4.5 0 0 1 4.5 4.5C9 8 4.5 12 4.5 12S0 8 0 4.5A4.5 4.5 0 0 1 4.5 0z"/><circle cx="4.5" cy="4.5" r="1.6" fill="var(--footer)"/></svg><span>Lorem ipsum dolor sit<br>amet, consectetuer<br>adipiscing elit.</span></div>
    <div class="row"><svg width="10" height="10" viewBox="0 0 10 10" fill="none" stroke="var(--orange)" stroke-width="1.4"><circle cx="5" cy="5" r="4"/><path d="M3.5 3.5l1 2 2 1"/></svg><span>123 456 7890</span></div>
    <div class="row"><svg width="10" height="8" viewBox="0 0 10 8" fill="var(--orange)"><rect width="10" height="8" rx="1"/><path d="M0 1l5 3.5L10 1" stroke="var(--footer)" fill="none"/></svg><span>support@hcsg-mail.com</span></div>
  </div>
</footer>
<div class="abs base">COPYRIGHT 2014 © HCSG<br>ALL RIGHTS RESERVED</div>
</body>
</html>
```